IRON PEAK TRAINING- Shooting Range!!!And virtual shooting range!!!

We are looking to do a clean cut web page for shooting range. We have indoor shooting simulator, retail store that sales accessories and pistols, rifles and shot guns. We are membership based for indoor shooting range Only and virtual shooting is open to public as well as retail store. We also specialize in shooting training classes and CWP classes.
Updates

Thank you for your patience. We are working with a busy travel schedule. We will be making final decisions tomorrow and moving forward with getting this launched. Regards, Gerald

Target Market(s)

Public and private entertainment

Industry/Entity Type

Training

Number of Pages Required

5+ page

Font styles to use
Sans Serif

Requirements
Must have
• Clean and easy approach we really like the website our friend has www.valormarkline.com please take a look at a lay out. We would like to also add onli member schedule that is available for shooting sections and that they can access and book them selvs.
Nice to have
• White, black, gray or red colors

```html
<!DOCTYPE html>
<html lang="en">
<head>
<meta charset="utf-8">
<title>Iron Peak Training LLC</title>
<link href="https://fonts.googleapis.com/css2?family=Raleway:wght@400;500;600;700&family=Open+Sans:wght@400;600&display=swap" rel="stylesheet">
<style>
:root{
  --red:#c8102e;
  --red-dark:#9b0c1f;
  --red-deep:#7a0a17;
  --ink:#2b2b2b;
  --body:#555;
  --muted:#8a8a8a;
  --footer-top:#4a4a4a;
  --footer-bottom:#262626;
  --bar:#1c1c1c;
  --white:#fff;
}
*{box-sizing:border-box;margin:0;padding:0}
html,body{width:1059px;height:1200px;overflow:hidden;background:var(--white)}
body{position:relative;font-family:"Open Sans",Arial,sans-serif;color:var(--body)}
.abs{position:absolute}

.brand{left:164px;top:22px;display:flex;align-items:center;gap:10px}
.brand-dot{width:56px;height:56px;border-radius:50%;background:var(--red)}
.brand-name{font-family:"Raleway",sans-serif;font-weight:700;font-size:25px;color:#8c8f93;line-height:1.05;letter-spacing:.5px}
.brand-name small{display:block;font-size:12px;letter-spacing:3px}

.nav{left:163px;top:94px;width:734px;height:37px;background:linear-gradient(#d3142f,#b80e26);display:flex}
.nav a{font-family:"Raleway",sans-serif;font-weight:600;font-size:12px;color:var(--white);text-decoration:none;display:flex;align-items:center;justify-content:center;border-right:1px solid rgba(0,0,0,.18)}
.nav a:last-child{border-right:0}
.nav a.active{background:var(--red-deep)}

.hero{left:163px;top:131px;width:734px;height:313px;background:#151515;overflow:hidden}
.hero-photo{position:absolute;left:220px;top:0;width:514px;height:313px;background:linear-gradient(90deg,#151515 0%,#4a4744 20%,#8d8a84 50%,#a9a59c 70%,#3c3a37 100%)}
.hero-text{position:absolute;left:45px;top:92px}
.hero-kicker{font-family:"Raleway",sans-serif;font-size:18px;color:var(--red);font-weight:500}
.hero-title{font-family:"Raleway",sans-serif;font-size:28px;color:var(--white);font-weight:500;margin-top:2px}
.hero-copy{font-size:10px;color:#ddd;line-height:13px;margin-top:8px;width:270px}
.dots{display:flex;gap:4px;margin-top:12px}
.dots i{width:11px;height:11px;border-radius:50%;background:#555}
.dots i:first-child{background:var(--white)}

.service{top:463px}
.service-photo{height:99px}
.service h3{font-family:"Raleway",sans-serif;font-weight:600;font-size:15px;color:var(--red);line-height:17px;margin:9px 2px 5px}
.service p{font-size:8px;line-height:12.5px;color:#444;margin:0 2px;width:165px}

.divider{left:148px;top:677px;width:764px;height:1px;background:#e6e6e6}

.about{left:165px;top:720px;width:480px}
.about h2{font-family:"Raleway",sans-serif;font-weight:500;font-size:21px;color:var(--ink)}
.about p{font-size:8px;line-height:13.5px;color:#666;margin-top:9px}
.btn-more{display:inline-block;margin-top:16px;background:linear-gradient(#c8102e,#a00d21);color:var(--white);font-size:9px;padding:7px 14px;border-radius:3px}

.booking{left:699px;top:715px;width:196px;height:165px;background:linear-gradient(var(--red),var(--red-dark));padding:18px 18px}
.booking h2{font-family:"Raleway",sans-serif;font-weight:500;font-size:15px;color:var(--white);margin-bottom:9px}
.field{height:22px;background:#f3f3f3;border:1px solid #ddd;font-size:8px;color:#666;padding:5px 9px;margin-bottom:5px}
.submit{display:inline-block;background:#000;color:var(--white);font-family:"Raleway",sans-serif;font-size:10px;font-weight:600;padding:7px 20px;margin-top:1px}

.footer{left:0;top:944px;width:1059px;height:204px;background:linear-gradient(var(--footer-top),var(--footer-bottom))}
.col{top:39px}
.col h4{font-family:"Raleway",sans-serif;font-weight:500;font-size:13px;color:var(--white);margin-bottom:5px}
.col li{list-style:none;font-size:10px;color:var(--muted);line-height:21.5px}
.socials{display:flex;gap:4px;margin-top:6px}
.socials i{width:16px;height:16px;background:#f1f1f1;border-radius:3px}
.foot-brand{left:696px;top:128px;display:flex;align-items:center;gap:8px;opacity:.5}
.foot-brand .brand-dot{width:52px;height:52px;background:#777}
.foot-brand .brand-name{font-size:20px;color:#888}
.foot-brand .brand-name small{font-size:9px}

.bar{left:0;top:1148px;width:1059px;height:52px;background:var(--bar);font-size:8px;color:#888;padding:18px 167px}
</style>
</head>
<body>

<header class="brand abs">
  <span class="brand-dot"></span>
  <span class="brand-name">IRON PEAK<small>TRAINING LLC</small></span>
</header>

<nav class="nav abs">
  <a class="active" style="width:81px">HOME</a>
  <a style="width:91px">ABOUT US</a>
  <a style="width:91px">TRAINING</a>
  <a style="width:138px">MEMBER BOOKING</a>
  <a style="width:127px">CWP CLASSES</a>
  <a style="width:105px">LOCATION</a>
  <a style="width:101px">CONTACT</a>
</nav>

<section class="hero abs">
  <div class="hero-photo" role="img" aria-label="Photo of an indoor shooting range lane with paper targets"></div>
  <div class="hero-text">
    <div class="hero-kicker">SED METUS AUGUE CONVALLIS</div>
    <div class="hero-title">CURABITUR TRISTIQUE</div>
    <p class="hero-copy">Suscipit leo massa sodales velit et scelerisque mi tortor at ipsum Proin orci odio commodo ac gravida non</p>
    <div class="dots"><i></i><i></i><i></i><i></i></div>
  </div>
</section>

<article class="service abs" style="left:163px;width:175px">
  <div class="service-photo" role="img" aria-label="Photo of a shooter in camouflage aiming at the simulator" style="background:linear-gradient(90deg,#3a4030,#5b6247 40%,#1e2220)"></div>
  <h3>INDOOR SHOOTING SIMULATOR</h3>
  <p>Fusce ultricies orci ac feugiat suscipit leo massa sodales velit et scelerisqu</p>
</article>
<article class="service abs" style="left:353px;width:170px">
  <div class="service-photo" role="img" aria-label="Photo of a shooting booth with a target in view" style="background:linear-gradient(90deg,#2a1c1c,#4a3430 50%,#1a1414)"></div>
  <h3>SALES ACCESSORIES</h3>
  <p>Fusce ultricies orci ac feugiat suscipit leo massa sodales velit et scelerisque mi tortor at ipsum cligula augue</p>
</article>
<article class="service abs" style="left:536px;width:174px">
  <div class="service-photo" role="img" aria-label="Photo of two tactical trainees practicing indoors" style="background:linear-gradient(90deg,#1b1b1d,#3b3b3e 50%,#1b1b1d)"></div>
  <h3>SHOOTING TRAINING</h3>
  <p>Fusce ultricies orci ac feugiat suscipit leo massa sodales velit et scelerisque mi tortor at ipsum cligula augue</p>
</article>
<article class="service abs" style="left:722px;width:174px">
  <div class="service-photo" role="img" aria-label="Photo of a dark grey armored vehicle outdoors" style="background:linear-gradient(90deg,#9aa596,#4c4f52 45%,#6b7c5e)"></div>
  <h3>CWP CLASSES</h3>
  <p>Fusce ultricies orci ac feugiat suscipit leo massa sodales velit et scelerisque mi tortor at ipsum cligula augue</p>
</article>

<div class="divider abs"></div>

<section class="about abs">
  <h2>ABOUT OUR COMPANY</h2>
  <p>Mauris vel lacus vitae felis vestibulum volutpat Etiam est nunc venenatis in tristique eu imperdiet ac nisl Cum sociis natoque penatibus et magnis dis parturient montes nascetur ridiculus mus In iaculis facilisis massa Etiam eu urna Sed porta Suspend-isse quam leo molestie sed luctus quis feugiat in pede Fusce tellus Sed metus augue convallis et</p>
  <p>Pellentesque faucibus Ut accumsan ultricies elit Maecenas at justo id velit placerat molestie Donec dictum lectus non odio Cras a ante vitae enim iaculis aliquam Mauris nunc quam venenatis nec euismod sit amet egestas Pellentesque faucibus Ut accumsan ultricies elit Maecenas at justo id velit placerat molestie Donec dictum lectus non odio</p>
  <span class="btn-more">READ MORE</span>
</section>

<form class="booking abs">
  <h2>MEMBER BOOKINGS</h2>
  <div class="field">Your Name</div>
  <div class="field">Email address</div>
  <div class="field">Phone no.</div>
  <span class="submit">SUBMIT</span>
</form>

<footer class="footer abs">
  <div class="col abs" style="left:169px">
    <h4>COMPANY</h4>
    <ul><li>About Us</li><li>Our Training</li><li>Our Classes</li><li>Membership</li></ul>
  </div>
  <div class="col abs" style="left:306px">
    <h4>SERVICES</h4>
    <ul><li>Indoor shooting simulator</li><li>Sales Accessories</li><li>CWP classes</li><li>Shooting</li></ul>
  </div>
  <div class="col abs" style="left:476px">
    <h4>ADDRESS</h4>
    <ul><li>482 Ridgeline Avenue #4B Texas 75301 TX</li><li>555.014.2290</li><li>info@ironpeaktraining.com</li></ul>
  </div>
  <div class="col abs" style="left:695px">
    <h4>GET IN TOUCH</h4>
    <ul><li>Please connect with us on these.</li></ul>
    <div class="socials"><i></i><i></i><i></i></div>
  </div>
  <div class="foot-brand abs">
    <span class="brand-dot"></span>
    <span class="brand-name">IRON PEAK<small>TRAINING LLC</small></span>
  </div>
</footer>

<div class="bar abs">© 2015 Company Name&nbsp; All right reserved&nbsp; Term of Use</div>

</body>
</html>
```